Smile club flyer design

I am launching an office smile club and would like a design that sits my branding and that is appealing to customers. I have a design (I need a new one) that has all the information.
My website is maplehavendentalcarekx.com
Brand color is green. The design can be any color

Target Market(s)

Ages 30+

Industry/Entity Type

Dental

Font styles to use
Serif

Requirements
Must have
• Appealing to patients

```html
<!DOCTYPE html>
<html lang="en">
<head>
<meta charset="utf-8">
<title>Maplehaven Dental Care – Smile Club Membership Flyer</title>
<link rel="stylesheet" href="https://fonts.googleapis.com/css2?family=Montserrat:wght@400;500;600;700;800&family=Kaushan+Script&display=swap">
<style>
  :root{
    --page-bg:#8a8b8f;
    --mint-light:#f4f8ec;
    --mint:#cfeadf;
    --teal:#14b8a6;
    --teal-deep:#0c9f91;
    --forest:#0f5a45;
    --forest-dark:#0b3b2e;
    --brand-green:#1a8a3e;
    --sage:#7c9d78;
    --sage-light:#9dbb8e;
    --gold:#d6b13a;
    --gold-dark:#7c5f14;
    --ink:#1d1d1d;
    --ink-soft:#3a3a3a;
    --script-gray:#8a8a8a;
    --white:#ffffff;
  }
  *{box-sizing:border-box;margin:0;padding:0}
  html,body{width:1200px;height:1200px;overflow:hidden}
  body{background:var(--page-bg);font-family:"Montserrat",sans-serif;position:relative}

  .flyer{
    position:absolute;left:152px;top:20px;width:896px;height:1160px;overflow:hidden;
    background:radial-gradient(ellipse at 30% 15%,var(--mint-light) 0%,#e5f2e4 45%,var(--mint) 100%);
  }
  .side-column{
    position:absolute;left:660px;top:0;width:236px;height:1160px;
    background:linear-gradient(160deg,var(--teal) 0%,#2cc3ae 55%,#3ccab4 100%);
  }
  .side-column__text{
    position:absolute;left:25px;top:135px;width:184px;color:var(--white);
    font-size:17.5px;line-height:21px;font-weight:500;
  }
  .portrait{
    position:absolute;left:590px;top:545px;width:306px;height:615px;
    border-radius:150px 0 0 0;
    background:linear-gradient(180deg,#6b4a36 0%,#c99a7e 35%,#e9d9cf 62%,#f7f5f1 100%);
  }

  .logo{position:absolute;left:46px;top:38px;text-align:center;color:var(--brand-green)}
  .logo__name{font-size:40px;font-weight:600;line-height:44px;letter-spacing:-.5px}
  .logo__sub{font-size:16px;font-weight:600;letter-spacing:5px;display:flex;align-items:center;gap:6px;justify-content:center}
  .logo__sub::before,.logo__sub::after{content:"";width:24px;height:2px;background:var(--brand-green)}

  .intro{position:absolute;left:52px;top:128px;font-family:"Kaushan Script",cursive;font-size:48px;color:var(--script-gray);transform:rotate(-4deg)}
  .title{position:absolute;left:44px;top:188px;font-size:80px;font-weight:800;color:var(--teal);letter-spacing:-2px;line-height:80px}
  .subtitle{position:absolute;left:46px;top:275px;font-size:40px;font-weight:600;letter-spacing:8px;color:var(--sage)}
  .tagline{
    position:absolute;left:0;top:324px;width:632px;height:37px;background:var(--gold);
    border-radius:0 19px 19px 0;color:var(--white);font-size:18px;font-weight:500;
    padding-left:48px;line-height:37px;
  }

  .tier{position:absolute;left:46px;height:var(--h);display:flex}
  .tier__panel{
    position:absolute;left:0;top:0;height:100%;width:var(--w);
    background:rgba(255,255,255,.55);box-shadow:0 3px 6px rgba(0,0,0,.12);
  }
  .tier__tab{
    position:relative;width:191px;height:100%;border-radius:38px 0 0 38px;
    color:var(--white);font-weight:700;font-size:21px;line-height:23px;
    padding-left:32px;display:flex;flex-direction:column;justify-content:center;
  }
  .tier__tag{color:var(--white);font-size:14px;width:70px;padding:5px 8px;border-radius:3px;margin-bottom:12px;background:#e0bf4a}
  .tier__price{position:relative;width:114px;padding-left:19px;display:flex;flex-direction:column;justify-content:center;font-size:25px;font-weight:700;line-height:26px}
  .tier__price small{font-size:17px;font-weight:400}
  .tier__list{position:relative;list-style:none;display:flex;flex-direction:column;justify-content:center;gap:5px;font-size:14px;line-height:16px;color:var(--ink-soft);width:var(--lw,270px)}
  .tier__list li{padding-left:17px;position:relative}
  .tier__list li::before{content:"";position:absolute;left:0;top:3px;border-left:8px solid var(--bullet);border-top:5px solid transparent;border-bottom:5px solid transparent}
  .tier__list .offer{font-family:"Kaushan Script",cursive;font-size:24px;color:var(--script-gray);margin-top:22px;line-height:28px}
  .tier__list .offer::before{top:10px}

  .tier--core{top:386px;--h:122px;--w:614px;--bullet:var(--teal)}
  .tier--core .tier__tab{background:linear-gradient(90deg,var(--teal-deep),var(--teal))}
  .tier--core .tier__price{color:var(--teal)}
  .tier--bright{top:519px;--h:109px;--w:614px;--bullet:var(--sage-light)}
  .tier--bright .tier__tab{background:linear-gradient(90deg,#55704f,var(--sage-light))}
  .tier--bright .tier__price{color:var(--sage-light)}
  .tier--perio{top:639px;--h:140px;--w:560px;--bullet:var(--forest-dark);--lw:235px}
  .tier--perio .tier__tab{background:linear-gradient(90deg,var(--forest-dark),var(--forest))}
  .tier--perio .tier__price{color:var(--forest)}
  .tier--refresh{top:789px;--h:139px;--w:560px;--bullet:var(--gold)}
  .tier--refresh .tier__tab{background:linear-gradient(90deg,var(--gold-dark),var(--gold) 70%);justify-content:flex-start;padding-top:16px}
  .tier--refresh .tier__price{color:var(--gold)}

  .cta{position:absolute;left:77px;top:960px}
  .cta__line{font-size:33px;font-weight:500;color:var(--ink)}
  .cta__phone{display:flex;align-items:center;gap:24px;margin-top:2px;font-size:45px;font-weight:800;color:var(--brand-green)}
  .divider{position:absolute;left:77px;top:1069px;width:433px;height:2px;background:#a9b5aa}
  .finance{position:absolute;left:85px;top:1082px;display:flex}
  .finance__title{font-size:16px;font-weight:700;color:var(--ink)}
  .finance__partners{display:flex;align-items:center;margin-top:8px}
  .partner{font-size:21px;font-weight:600;color:var(--ink)}
  .partner-sep{width:1px;height:32px;background:#777;margin:0 28px}
  .finance__plans{border-left:1px solid #777;margin-left:20px;padding-left:20px;font-size:15px;line-height:16px;color:var(--ink-soft);height:58px;display:flex;align-items:center}
  .footnote{
    position:absolute;left:564px;top:1117px;width:332px;height:21px;background:var(--brand-green);
    border-radius:10px 0 0 10px;color:var(--white);font-size:11px;line-height:21px;padding-left:28px;
  }
</style>
</head>
<body>
<main class="flyer">
  <div class="side-column">
    <p class="side-column__text">Providing personalized, high-quality dental care to the Maplehaven Farms community and surrounding areas in Kingsbury, TN.</p>
  </div>
  <div class="portrait" role="img" aria-label="Photo of a smiling woman with long brown hair in a white blouse"></div>

  <header class="logo">
    <div class="logo__name">Maplehaven</div>
    <div class="logo__sub">DENTAL CARE</div>
  </header>

  <p class="intro">Introducing</p>
  <h1 class="title">SMILE CLUB</h1>
  <p class="subtitle">MEMBERSHIP</p>
  <p class="tagline">AFFORDABLE DENTAL CARE - NO INSURANCE REQUIRED</p>

  <section class="tier tier--core">
    <div class="tier__panel"></div>
    <div class="tier__tab">Core Care<br>Preventive</div>
    <div class="tier__price">$39 /<small>Month</small></div>
    <ul class="tier__list">
      <li>Comprehensive Annual Exam</li>
      <li>2 Professional Cleanings per Year</li>
      <li>Routine Bitewing X-rays</li>
      <li>10% Savings on Treatment</li>
    </ul>
  </section>

  <section class="tier tier--bright">
    <div class="tier__panel"></div>
    <div class="tier__tab">Bright<br>Cosmetic</div>
    <div class="tier__price">$59 /<small>Month</small></div>
    <ul class="tier__list">
      <li>Annual In-Office Whitening (Top &amp; Bottom)</li>
      <li>Custom Whitening Trays</li>
      <li>15% Savings on Elective Treatment</li>
    </ul>
  </section>

  <section class="tier tier--perio">
    <div class="tier__panel"></div>
    <div class="tier__tab">Total Smile<br>Periodontal</div>
    <div class="tier__price">$89 /<small>Month</small></div>
    <ul class="tier__list">
      <li>3-4 Perio Maintenance Visits<br>per Year</li>
      <li>1 Comprehensive Exam</li>
      <li>Diagnostic X-rays</li>
      <li>15% Savings on Restorative &amp;<br>Elective Care</li>
    </ul>
  </section>

  <section class="tier tier--refresh">
    <div class="tier__panel"></div>
    <div class="tier__tab"><span class="tier__tag">NEW</span>SMILE<br>Refresh<br>Package</div>
    <div class="tier__price">$499</div>
    <ul class="tier__list">
      <li>Cleaning +<br>Comprehensive Exam +<br>Whitening</li>
      <li class="offer">Limited Time Offer</li>
    </ul>
  </section>

  <section class="cta">
    <p class="cta__line">Join Smile Club Today!</p>
    <p class="cta__phone">
      <svg width="36" height="36" viewBox="0 0 24 24" aria-hidden="true"><path fill="#d6b13a" d="M6.6 10.8c1.4 2.8 3.8 5.1 6.6 6.6l2.2-2.2c.3-.3.7-.4 1-.2 1.1.4 2.3.6 3.6.6.6 0 1 .4 1 1V20c0 .6-.4 1-1 1C10.6 21 3 13.4 3 4c0-.6.4-1 1-1h3.5c.6 0 1 .4 1 1 0 1.3.2 2.5.6 3.6.1.3 0 .7-.2 1L6.6 10.8z"/></svg>
      865-555-0172
    </p>
  </section>
  <div class="divider"></div>
  <section class="finance">
    <div>
      <p class="finance__title">Flexible Financing For Treatment:</p>
      <div class="finance__partners">
        <span class="partner">MediFlex</span>
        <span class="partner-sep"></span>
        <span class="partner">Paywell</span>
      </div>
    </div>
    <p class="finance__plans">Payment<br>Plans<br>Available</p>
  </section>
  <p class="footnote">*$49 Lifetime Activation Fee (Non-Refundable)</p>
</main>
</body>
</html>
```